Card design for orthopaedic surgeons working as The Brightwater Joint Centre

Business cards, letterhead

Colors

Designer to choose colors to be used in the design.

Requirements
Must have
• Late addition.
• Cards letterhead must have logos of
• Crestmoor Lindell College of Surgeons
• Varenwood Bone Health Association
Nice to have
• Back of card to have space for appointment time to be added by hand and some blank space for writing incidental other notes.

```html
<!DOCTYPE html>
<html lang="en">
<head>
<meta charset="utf-8">
<title>The Brightwater Joint Centre – Letterhead</title>
<link rel="stylesheet" href="https://fonts.googleapis.com/css2?family=Montserrat:wght@400&family=Lato:wght@400;700&display=swap">
<style>
  :root {
    --backdrop: #e7e4e0;
    --paper: #ffffff;
    --navy: #0f2c47;
    --footer-navy: #0e3350;
    --sky: #5aa6dc;
    --rule: #5d6e7d;
    --contact-text: #4a4f55;
    --wave-light: #c3dbf1;
    --wave-grey: #8a8f9f;
  }
  * { margin: 0; padding: 0; box-sizing: border-box; }
  html, body {
    width: 1200px;
    height: 1200px;
    overflow: hidden;
    background: var(--backdrop);
  }
  .letterhead {
    position: absolute;
    left: 197px;
    top: 30px;
    width: 806px;
    height: 1140px;
    background: var(--paper);
    box-shadow: 0 6px 22px rgba(0, 0, 0, 0.18);
  }
  .brand-name {
    position: absolute;
    left: 26px;
    top: 72px;
    font-family: "Montserrat", sans-serif;
    font-weight: 400;
    font-size: 31px;
    letter-spacing: -0.6px;
    color: var(--navy);
    white-space: nowrap;
  }
  .contact-list {
    position: absolute;
    left: 627px;
    top: 66px;
    list-style: none;
    font-family: "Lato", sans-serif;
    font-size: 13.5px;
    line-height: 16px;
    color: var(--contact-text);
  }
  .contact-list li {
    display: flex;
    align-items: center;
    gap: 6px;
  }
  .contact-icon {
    width: 11px;
    height: 11px;
    flex: none;
  }
  .header-rule {
    position: absolute;
    left: 0;
    top: 142px;
    width: 100%;
    height: 1.5px;
    background: var(--rule);
  }
  .footer-decoration {
    position: absolute;
    left: 0;
    top: 935px;
    width: 100%;
    height: 140px;
    background: linear-gradient(180deg, rgba(195, 219, 241, 0) 0%, rgba(195, 219, 241, 0.45) 60%, rgba(138, 143, 159, 0.18) 100%);
  }
  .footer-band {
    position: absolute;
    left: 0;
    bottom: 0;
    width: 100%;
    height: 60px;
    background: var(--footer-navy);
    display: flex;
    align-items: flex-start;
    justify-content: center;
    padding-top: 10px;
  }
  .footer-address {
    font-family: "Lato", sans-serif;
    font-weight: 700;
    font-size: 13px;
    color: #ffffff;
  }
</style>
</head>
<body>
  <main class="letterhead">
    <header>
      <div class="brand-name">The Brightwater Joint Centre</div>
      <ul class="contact-list">
        <li>
          <svg class="contact-icon" viewBox="0 0 12 12" aria-hidden="true">
            <path d="M1 4.5 C1 2.5 11 2.5 11 4.5 L11 5.5 L8.5 5.5 L8.5 4.5 L3.5 4.5 L3.5 5.5 L1 5.5 Z" fill="var(--navy)"/>
            <path d="M3 6.5 L9 6.5 L10 10 L2 10 Z" fill="var(--navy)"/>
          </svg>
          <span>012.1234 567</span>
        </li>
        <li>
          <svg class="contact-icon" viewBox="0 0 12 12" aria-hidden="true">
            <rect x="1" y="4" width="10" height="7" fill="none" stroke="var(--navy)" stroke-width="1.2"/>
            <path d="M1 4 L6 1 L11 4 M1 4 L6 8 L11 4" fill="none" stroke="var(--navy)" stroke-width="1.2"/>
          </svg>
          <span>info@yourdomain.com</span>
        </li>
        <li>
          <svg class="contact-icon" viewBox="0 0 12 12" aria-hidden="true">
            <circle cx="6" cy="6" r="5" fill="none" stroke="var(--navy)" stroke-width="1.1"/>
            <ellipse cx="6" cy="6" rx="2.2" ry="5" fill="none" stroke="var(--navy)" stroke-width="1"/>
            <path d="M1 6 H11 M2 3.5 H10 M2 8.5 H10" stroke="var(--navy)" stroke-width="0.9"/>
          </svg>
          <span>www.yourdomain.com</span>
        </li>
      </ul>
    </header>
    <div class="header-rule"></div>

    <div class="footer-decoration" role="img" aria-label="Soft blue and grey decorative band above the footer"></div>

    <footer class="footer-band">
      <p class="footer-address">1023 Street Here, Suite 123, City Name, State 1234</p>
    </footer>
  </main>
</body>
</html>
```